business card design for a plumbing contractor

i need a double business card for a plumbing business, our initial service is residential Sewer Drain Cleaning.

Target Market(s)

other plumbing Business

Industry/Entity Type

Plumbing

Contact Information for Business Card

www.PipeworksTopMark.example- 5307218394-

Font styles to use
Serif

Colors
ec1f27
0455a3

```html
<!DOCTYPE html>
<html lang="en">
<head>
<meta charset="utf-8">
<title>Pipeworks Top Mark – Business Card</title>
<link href="https://fonts.googleapis.com/css2?family=Roboto+Condensed:wght@400;700&family=Roboto:wght@400;700&display=swap" rel="stylesheet">
<style>
  :root {
    --brand-red: #dc3a32;
    --accent-red: #ec1f27;
    --ink-grey: #8a8580;
    --text-dark: #3a3a3a;
    --paper: #fbfbfb;
    --backdrop: #e6e3df;
  }
  * { margin: 0; padding: 0; box-sizing: border-box; }
  html, body {
    width: 1200px; height: 886px; overflow: hidden;
    background: var(--backdrop);
    font-family: "Roboto Condensed", "Arial Narrow", sans-serif;
  }
  .stage {
    position: relative; width: 1200px; height: 886px;
    display: flex; align-items: center; justify-content: center; gap: 50px;
  }
  .card {
    position: relative; width: 520px; height: 297px;
    border-radius: 18px; overflow: hidden;
    box-shadow: 0 6px 18px rgba(0,0,0,0.18);
  }
  .card-front { background: var(--paper); }
  .card-back { background: var(--brand-red); color: #fff; }

  .holder { position: absolute; top: 34px; right: 40px; text-align: left; }
  .holder-name {
    color: var(--accent-red); font-weight: 700; font-size: 21px; letter-spacing: 0.5px;
  }
  .holder-role {
    color: var(--ink-grey); font-size: 14px; letter-spacing: 0.6px; margin-top: 2px;
  }

  .brand-name {
    position: absolute; left: 40px; bottom: 104px;
    color: var(--ink-grey); font-weight: 700; font-size: 28px; line-height: 1;
  }

  .contact-list { position: absolute; left: 40px; bottom: 28px; list-style: none; }
  .contact-item {
    display: flex; align-items: center; gap: 8px;
    color: var(--text-dark); font-size: 13.5px; line-height: 22px;
  }
  .contact-icon { width: 12px; height: 12px; flex: none; }

  .back-title {
    position: absolute; left: 40px; top: 34px;
    font-family: "Roboto", Arial, sans-serif; font-weight: 700;
    font-size: 34px; line-height: 0.98;
  }
  .service-list {
    position: absolute; left: 40px; top: 120px; list-style: none;
    font-size: 14px; line-height: 20px;
  }
  .service-list li::before { content: "•"; margin-right: 6px; }
</style>
</head>
<body>
<main class="stage">
  <section class="card card-front" aria-label="Card front">
    <div class="holder">
      <p class="holder-name">DALE MORROW</p>
      <p class="holder-role">CEO/FOUNDER</p>
    </div>
    <p class="brand-name">Pipeworks Top Mark</p>
    <ul class="contact-list">
      <li class="contact-item">
        <svg class="contact-icon" viewBox="0 0 12 12"><path d="M2.5 1h2l1 2.5-1.3 1a6 6 0 0 0 3.3 3.3l1-1.3 2.5 1v2c0 .8-.7 1.5-1.5 1.5A9.5 9.5 0 0 1 1 2.5C1 1.7 1.7 1 2.5 1z" fill="var(--accent-red)"/></svg>
        5307218394
      </li>
      <li class="contact-item">
        <svg class="contact-icon" viewBox="0 0 12 12"><rect x="0.5" y="2" width="11" height="8" rx="1" fill="var(--accent-red)"/><path d="M1 2.8 6 6.5 11 2.8" fill="none" stroke="#fff" stroke-width="1"/></svg>
        Dispatcher@PipeworksTopMark.example
      </li>
      <li class="contact-item">
        <svg class="contact-icon" viewBox="0 0 12 12"><circle cx="6" cy="6" r="5.5" fill="var(--accent-red)"/><path d="M0.5 6h11M6 0.5c-2.5 3-2.5 8 0 11M6 0.5c2.5 3 2.5 8 0 11" fill="none" stroke="#fff" stroke-width="0.8"/></svg>
        www.PipeworksTopMark.example
      </li>
    </ul>
  </section>

  <section class="card card-back" aria-label="Card back">
    <h1 class="back-title">Pipeworks<br>Top Mark</h1>
    <ul class="service-list">
      <li>Sewer Drain Cleaning</li>
      <li>Maintenance</li>
      <li>Trenchless Pipe Repair</li>
    </ul>
  </section>
</main>
</body>
</html>
```